Marlow Estate Fixers (Handyman / Home Improvement Company)

Looking for a double sided professional looking business card with Logo attached to be highlighted on one side and throwing in an image of a handyman as an option would be nice to see as well. We are a company focused on providing quality Handyman and Home improvement services in a timely manner that is done right the first time with integrity

Industry/Entity Type

Handyman / Home Improvement

Contact Information for Business Card

(LOGO, Name, Mobile and office phone numbers, email) on front side of card, (the words "The SOLUTION to all of your Handyman and Home Improvement needs" followed by "Family Owned and Operated" at the very bottom) on the back.

Colors
EB3D1F
EC4F4E
F09395
F8D3D4
FCEDEE

Requirements
Must have
• Red, Gray, Black Color scheme
Should not have
• No Yellow or Blue colors

```html
<!DOCTYPE html>
<html lang="en">
<head>
<meta charset="utf-8">
<title>Marlow Estate Fixers – Business Card</title>
<link href="https://fonts.googleapis.com/css2?family=Montserrat:wght@300;400;600;700;800&display=swap" rel="stylesheet">
<style>
  :root {
    --stage: #242426;
    --card-dark: #1d1d21;
    --card-dark-2: #28282d;
    --red: #eb2b2e;
    --red-deep: #c41f22;
    --white: #ffffff;
    --muted: #a7a7ad;
  }
  * { box-sizing: border-box; margin: 0; padding: 0; }
  html, body {
    width: 1200px; height: 800px; overflow: hidden;
    background: var(--stage);
    font-family: "Montserrat", sans-serif;
    color: var(--white);
  }
  .stage {
    position: relative; width: 1200px; height: 800px;
    display: flex; align-items: center; justify-content: center; gap: 48px;
  }
  .card {
    position: relative; width: 540px; height: 310px;
    border-radius: 22px; overflow: hidden;
    background: var(--card-dark);
    box-shadow: 0 6px 0 var(--red), 0 18px 30px rgba(0,0,0,.45);
  }

  /* Back side */
  .card-back .pattern-fill {
    position: absolute; inset: 0;
    background: radial-gradient(circle at 50% 45%, var(--card-dark-2) 0%, var(--card-dark) 75%);
  }
  .card-back .brand {
    position: absolute; left: 0; right: 0; top: 92px;
    display: flex; align-items: center; justify-content: center; gap: 12px;
  }
  .brand-dot {
    width: 22px; height: 22px; border-radius: 50%; background: var(--red);
  }
  .card-back .brand-name {
    font-weight: 800; font-size: 28px; letter-spacing: 1px;
    text-transform: uppercase; color: var(--white);
  }
  .card-back .family {
    position: absolute; left: 0; right: 0; top: 186px;
    text-align: center; color: var(--red); font-size: 15px; font-weight: 400;
  }
  .card-back .tagline {
    position: absolute; left: 0; right: 0; top: 214px;
    text-align: center; font-size: 13.5px; font-weight: 400; color: var(--white);
  }

  /* Front side */
  .card-front .edge-strip {
    position: absolute; left: 0; top: 44px; width: 12px; height: 130px; background: var(--red);
  }
  .card-front .logo-panel { position: absolute; inset: 0; }
  .card-front .panel-brand {
    position: absolute; right: 24px; top: 0; bottom: 0; width: 200px;
    display: flex; flex-direction: column; align-items: center; justify-content: center; gap: 12px;
  }
  .panel-brand .brand-square { width: 20px; height: 20px; background: #141417; }
  .panel-brand .brand-name {
    font-weight: 800; font-size: 22px; line-height: 1.15; text-align: center;
    text-transform: uppercase; color: #141417;
  }
  .person { position: absolute; left: 34px; top: 42px; }
  .person-name { font-size: 30px; color: var(--red); line-height: 1; }
  .person-name .first { font-weight: 800; }
  .person-name .last { font-weight: 300; }
  .person-title { margin-top: 6px; font-size: 14px; font-weight: 700; }
  .address {
    position: absolute; left: 34px; top: 150px;
    font-size: 13px; line-height: 1.4; font-weight: 400;
  }
  .contacts {
    position: absolute; left: 34px; top: 200px; list-style: none;
    font-size: 12.5px; line-height: 1.55;
  }
  .contacts li { display: flex; align-items: center; gap: 8px; }
  .contacts svg { width: 12px; height: 12px; flex: none; }
  .accent { color: var(--red); }
</style>
</head>
<body>
<main class="stage">

  <section class="card card-back" aria-label="Business card back">
    <div class="pattern-fill" role="img" aria-label="Repeating embossed brand-mark pattern on dark background"></div>
    <div class="brand">
      <span class="brand-dot"></span>
      <span class="brand-name">Marlow Estate Fixers</span>
    </div>
    <p class="family">Family Owned and Operated</p>
    <p class="tagline">Your SOLUTION to all of your Handyman and Home Improvement needs</p>
  </section>

  <section class="card card-front" aria-label="Business card front">
    <svg class="logo-panel" viewBox="0 0 540 310" preserveAspectRatio="none" aria-hidden="true">
      <polygon points="300,0 540,0 540,310 330,310" fill="var(--red)"/>
      <polygon points="258,0 300,0 330,310 288,310" fill="#2a2a2f"/>
    </svg>
    <div class="panel-brand">
      <span class="brand-square"></span>
      <span class="brand-name">Marlow<br>Estate<br>Fixers</span>
    </div>
    <div class="edge-strip"></div>

    <div class="person">
      <p class="person-name"><span class="first">Ilona</span> <span class="last">Varga</span></p>
      <p class="person-title">Founder &amp; CEO</p>
    </div>

    <p class="address">4180 Birchmont Ave. Suite 310<br>Millbrook, OH 44820</p>

    <ul class="contacts">
      <li>
        <svg viewBox="0 0 12 12"><rect x="3" y="0.5" width="6" height="11" rx="1.2" fill="none" stroke="var(--red)" stroke-width="1.2"/></svg>
        (555) 214-6083
      </li>
      <li>
        <svg viewBox="0 0 12 12"><path d="M2 1 L4.5 1 L5.5 3.5 L4 4.8 C4.8 6.6 5.6 7.4 7.2 8 L8.5 6.5 L11 7.5 L11 10 C6 10.5 1.5 6 2 1 Z" fill="var(--red)"/></svg>
        (555) 214-9090
      </li>
      <li>
        <svg viewBox="0 0 12 12"><circle cx="6" cy="6" r="5" fill="none" stroke="var(--red)" stroke-width="1.2"/><path d="M1 6 H11 M6 1 C3.5 3.5 3.5 8.5 6 11 M6 1 C8.5 3.5 8.5 8.5 6 11" fill="none" stroke="var(--red)" stroke-width="0.9"/></svg>
        <span>www.<span class="accent">marlowfixers</span>.com</span>
      </li>
      <li>
        <svg viewBox="0 0 12 12"><rect x="0.8" y="2.5" width="10.4" height="7.5" fill="none" stroke="var(--red)" stroke-width="1.2"/><path d="M0.8 2.5 L6 6.8 L11.2 2.5" fill="none" stroke="var(--red)" stroke-width="1.2"/></svg>
        <span>info@<span class="accent">marlowfixers</span>.com</span>
      </li>
    </ul>
  </section>

</main>
</body>
</html>
```